Stonebrace Business Card Design

The Stonebrace Co is an aggregate (crushing) equipment dealer serving Western Canadian provinces. Stonebrace is a distributor of aggregate equipment for different manufacturers.

We are looking to change and update the existing business card which has been used since the existence of the company. A copy of existing card has been attached for reference. The Stonebrace Co logo we want to remain the same and we want the green color to remain the same.

We are wanting something new with a different look. A refreshing card to show a new modern and updated look. No longer wanting to have the manufacturers on the back of the card but something more like our logo on the back of the card with a statement like "Crushing Solutions"

ideas could be:
- card can be different colors on front and back
- front or reverse of the card could possibly be the green color with the logo in black

Target Market(s)

Owners of Aggregate/Crushing companies

Contact Information for Business Card

see above

Requirements
Must have
• - logo to remain same along with same font within logo
• - green color to remain same
Nice to have
• as noted above under project description
Should not have

```html
<!DOCTYPE html>
<html lang="en">
<head>
<meta charset="utf-8">
<title>The Stonebrace Co – Business Card</title>
<link rel="stylesheet" href="https://fonts.googleapis.com/css2?family=Roboto:wght@400;500;700&family=Roboto+Condensed:wght@700&display=swap">
<style>
  :root {
    --backdrop: #5a4a3c;
    --card-white: #f2f2f2;
    --ink: #231f20;
    --brand-green: #8a8a08;
    --text-grey: #555555;
    --rule-grey: #777777;
    --white: #ffffff;
  }
  * { margin: 0; padding: 0; box-sizing: border-box; }
  html, body {
    width: 1200px; height: 960px; overflow: hidden;
    background: var(--backdrop);
    font-family: "Roboto", Arial, sans-serif;
  }
  .card {
    position: absolute;
    width: 600px; height: 343px;
    border-radius: 18px;
    overflow: hidden;
  }
  .card-front { left: 314px; top: 113px; background: var(--card-white); }
  .card-back { left: 311px; top: 472px; background: var(--brand-green); }

  .name-band {
    position: absolute; right: 0; top: 23px;
    width: 212px; height: 70px;
    background: var(--ink);
    border-radius: 35px 0 0 35px;
  }
  .holder-name {
    position: absolute; right: 34px; top: 42px;
    font-family: "Roboto Condensed", "Arial Narrow", sans-serif;
    font-weight: 700; font-size: 21px; color: var(--brand-green);
    text-align: right; letter-spacing: 0.2px;
  }
  .holder-title {
    position: absolute; right: 34px; top: 68px;
    font-size: 14px; font-weight: 500; color: var(--white);
  }

  .contact-list {
    position: absolute; left: 30px; top: 112px;
    list-style: none;
  }
  .contact-list li {
    display: flex; align-items: center;
    height: 19px;
    font-size: 14px; color: var(--text-grey);
  }
  .contact-icon { width: 13px; height: 13px; margin-right: 9px; fill: var(--brand-green); }

  .dotted-rule {
    position: absolute; left: 30px;
    border-top: 2px dotted var(--rule-grey);
    height: 0;
  }
  .rule-one { top: 213px; width: 177px; }
  .rule-two { top: 268px; width: 208px; }

  .address {
    position: absolute; left: 30px; top: 226px;
    font-size: 14px; line-height: 19px; color: var(--text-grey);
    font-style: normal;
  }
  .company-name-front {
    position: absolute; left: 30px; top: 283px;
    font-size: 18px; font-weight: 700; color: var(--ink);
    letter-spacing: 0.2px;
  }

  .brand-lockup {
    position: absolute; left: 0; right: 0; top: 160px;
    display: flex; justify-content: center; align-items: center;
  }
  .brand-dot {
    width: 26px; height: 26px; border-radius: 50%;
    background: var(--ink); margin-right: 14px;
  }
  .brand-name {
    font-size: 22px; font-weight: 700; color: var(--ink);
    letter-spacing: 0.2px;
  }
  .tagline {
    position: absolute; left: 0; right: 0; top: 292px;
    text-align: center;
    font-size: 14px; font-weight: 700; color: var(--ink);
  }
</style>
</head>
<body>
  <section class="card card-front">
    <div class="name-band"></div>
    <p class="holder-name">DALE MARREN</p>
    <p class="holder-title">CEO/FOUNDER</p>

    <ul class="contact-list">
      <li><svg class="contact-icon" viewBox="0 0 16 16"><path d="M3 1l3 3-1.5 2c1 2 3 4 5 5l2-1.5 3 3-2 2C7 14 2 9 1 3z"/></svg>780.555.0142</li>
      <li><svg class="contact-icon" viewBox="0 0 16 16"><path d="M4 0h8a1 1 0 0 1 1 1v14a1 1 0 0 1-1 1H4a1 1 0 0 1-1-1V1a1 1 0 0 1 1-1zm1 2v10h6V2z"/></svg>780.555.0187</li>
      <li><svg class="contact-icon" viewBox="0 0 16 16"><path d="M4 1h8v4H4zM1 6h14v6h-2v3H3v-3H1zm4 4v3h6v-3z"/></svg>780.555.0163</li>
      <li><svg class="contact-icon" viewBox="0 0 16 16"><path d="M1 4h14v9H1zm1 1l6 4 6-4z"/></svg>dale@stonebr.com</li>
      <li><svg class="contact-icon" viewBox="0 0 16 16"><circle cx="8" cy="8" r="7"/></svg>www.stonebrace.ca</li>
    </ul>

    <div class="dotted-rule rule-one"></div>
    <address class="address">2318- 52B Avenue<br>Nisku, Alberta T9E 4K2</address>
    <div class="dotted-rule rule-two"></div>
    <p class="company-name-front">THE STONEBRACE CO.</p>
  </section>

  <section class="card card-back">
    <div class="brand-lockup">
      <span class="brand-dot"></span>
      <span class="brand-name">THE STONEBRACE CO.</span>
    </div>
    <p class="tagline">Crushing Solutions</p>
  </section>
</body>
</html>
```